Flyer für Verkauf von Radondetektoren
Zielgruppe
Ich verkaufe Radondetektoren zur Messung von Radon in Innenräumen. Zielgruppe sind Privatpersonen, Firmen, Genossenschaften und andere Hauseigentümer.
Aufgabenstellung
Ich brauche das Design für meine Messanleitung.
Kreativ - modern - weniger kann mehr sein
Struktur ist wichtigt, es soll also einfach sein zu lesen und zu verstehen, was gemacht werden soll. Können Bulletpoints, Icons mit eingebracht werden.
Wichtig ist auch, dass die beiden Logos 'Luftprüfer.de' und TESTOVAL' auf der Messanleitung vorhanden sind. Wobei 'Luftprüfer.de' das Hauptlogo ist.
DIN format dachte ich A4 beidseitig (Text müsste also auf diese Grösse angepasst werden).
Kann natürlich auch Flyer-Format sein oder andere Vorschläge!
Bildmaterial gibt es auf unsere Homepage https://luftprüfer.de und https://luftkontroll.se . Diese haben wir bereits gekauft und können verwendet werden. Ich lade sie den bei Bedarf hoch. Es können natürlich auch andere Vorschläge kommen.

```html
<!DOCTYPE html>
<html lang="de">
<head>
<meta charset="utf-8">
<title>Messanleitung – Luftprüfer.de</title>
<link rel="stylesheet" href="https://fonts.googleapis.com/css2?family=Montserrat:ital,wght@0,400;0,500;0,600;0,700;0,800;1,700&family=Fredoka:wght@600&display=swap">
<style>
:root{
  --bg:#c9c9c9;
  --paper:#ffffff;
  --ink:#1d1d1b;
  --muted:#4a4a4a;
  --orange:#e8a310;
  --orange-text:#e39b0b;
  --link:#1a8fd6;
  --faint:#fbefd0;
  --dots:#c9c9c9;
}
*{box-sizing:border-box;margin:0;padding:0}
html,body{width:1200px;height:2400px;overflow:hidden}
body{background:var(--bg);font-family:"Montserrat",sans-serif;color:var(--ink);position:relative}
.brand{display:flex;align-items:center;gap:10px;font-family:"Montserrat",sans-serif;font-weight:500;color:var(--ink);white-space:nowrap}
.brand-dot{border-radius:50%;background:var(--orange);flex:none}
.board-head{position:absolute;left:128px;top:88px}
.board-head .brand{font-size:44px}
.board-head .brand-dot{width:40px;height:40px}
.spread{position:absolute;left:127px;width:946px;height:668px;background:var(--paper);box-shadow:0 6px 14px rgba(0,0,0,.25);display:flex}
.spread-1{top:198px}
.spread-2{top:910px}
.page{position:relative;width:473px;height:100%;padding:0 38px;font-size:10px;line-height:1.28;color:var(--muted)}
.deco{position:absolute;background:var(--faint);opacity:.6;border-radius:8px}
.tag-left{position:absolute;left:0;top:46px;background:var(--orange);color:#fff;font-family:"Fredoka",sans-serif;font-size:22px;padding:0 16px 0 40px;height:30px;line-height:30px;border-radius:0 16px 16px 0}
.notes{position:absolute;left:40px;right:60px;top:123px;list-style:none}
.notes li{font-weight:700;color:var(--ink);font-size:13.2px;line-height:1.22;margin-bottom:22px;padding-left:9px;position:relative}
.notes li::before{content:"•";position:absolute;left:0}
.hl{color:var(--orange-text)}
a,.url{color:var(--link);text-decoration:underline}
.legal{position:absolute;left:40px;top:490px;font-size:13px;line-height:1.3;color:var(--ink)}
.copy{position:absolute;left:40px;top:570px;font-size:9.5px;line-height:1.35;color:var(--muted)}
.foot-logos{position:absolute;left:40px;right:32px;bottom:20px;display:flex;justify-content:space-between;align-items:center}
.foot-logos .brand{font-size:13px;gap:5px}
.foot-logos .brand-dot{width:12px;height:12px}
.edge-dots{position:absolute;top:18px;bottom:18px;border-left:2px dotted var(--dots)}
.head-logos{position:absolute;left:38px;right:0;top:30px;display:flex;justify-content:space-between;align-items:center;padding-right:14px}
.head-logos .brand{font-size:22px;gap:6px}
.head-logos .brand-dot{width:22px;height:22px}
.head-logos .partner{font-size:18px}
.title{position:absolute;left:38px;top:96px;font-weight:800;font-size:19px;color:var(--ink);letter-spacing:.3px}
.subtitle{position:absolute;left:38px;top:126px;font-size:11.5px;line-height:1.3;color:var(--muted)}
.hero{position:absolute;right:0;top:72px;width:232px;height:120px;background:linear-gradient(180deg,#fff 0%,#b9a6d8 40%,#7fbf5a 80%,#5f9f3f 100%);border-radius:40px 0 0 0}
.hero-line{position:absolute;left:38px;right:0;top:184px;border-top:2px solid var(--orange)}
.step{position:absolute;left:38px;right:18px}
.step h3{font-size:12.5px;font-weight:700;color:var(--ink);line-height:1.25;margin-bottom:10px;letter-spacing:.2px}
.step p{margin-bottom:4px}
.step b{color:var(--ink)}
.step-tag{position:absolute;right:0;background:var(--orange);color:#fff;font-family:"Fredoka",sans-serif;font-size:22px;height:28px;line-height:28px;padding:0 24px 0 14px;border-radius:14px 0 0 14px}
.sub{font-weight:700;color:var(--ink);font-size:12.5px;margin:10px 0 6px}
.kind{color:var(--orange-text);font-weight:700;font-size:11px;margin:6px 0 5px}
.kind::before{content:"▸ ";font-size:9px}
.em{font-weight:700;font-style:italic;color:var(--ink)}
.dash{padding-left:7px;position:relative;margin-bottom:5px}
.dash::before{content:"·";position:absolute;left:0;font-weight:800}
.addr{color:var(--ink);font-weight:700;margin:8px 0}
.caption{position:absolute;left:0;right:0;top:1596px;text-align:center;font-size:25px;line-height:1.3;color:var(--ink);font-weight:400}
.board-foot{position:absolute;right:86px;top:2250px}
.board-foot .brand{font-size:38px;color:#1d4f91}
.board-foot .brand-dot{width:34px;height:34px;background:#1d4f91}
</style>
</head>
<body>

<header class="board-head">
  <div class="brand"><span class="brand-dot"></span>Luftprüfer.de</div>
</header>

<section class="spread spread-1">
  <div class="page page-back">
    <div class="deco" role="img" aria-label="Faint hand pointing upward" style="left:380px;top:44px;width:70px;height:130px"></div>
    <div class="tag-left">Wichtige Hinweise</div>
    <ul class="notes">
      <li>Bitte beachten Sie, dass die Radonmessung innerhalb von 15 Monaten nach Kaufdatum abgeschlossen sein muss.</li>
      <li>Versuchen Sie <span class="hl">nicht</span> das Gehäuse der Detektoren zu öffnen und platzieren Sie diese immer außer Reichweite von Kindern.</li>
      <li>Während der gesamten Messdauer dürfen die Detektoren nicht an einem anderen Ort umplatziert werden.</li>
      <li>Durch die Anmeldung auf der Website <span class="url">https://kunden.testoval.se/de</span> und die Eingabe der erforderlichen Daten bestätigt der/die Wohnungseigentümer*in/Messverantwortliche, dass er/sie die Messanleitung befolgt hat und die Detektoren gemäß den Anweisungen korrekt platziert wurden.</li>
    </ul>
    <p class="legal"><span class="hl">Datenschutz (GDPR),</span> Impressum und AGBs:<br>Mehr Information dazu finden Sie unter<br>www.luftprüfer.de</p>
    <p class="copy"><span class="hl">Copyright ©</span> 2023 Nordluft Mätteknik AB<br>– Alle Rechte vorbehalten<br>https://www.luftprüfer.de</p>
    <div class="foot-logos">
      <div class="brand partner"><span class="brand-dot"></span>TESTOVAL</div>
      <div class="brand"><span class="brand-dot"></span>Luftprüfer.de</div>
    </div>
  </div>

  <div class="page page-front">
    <div class="edge-dots" style="right:26px;top:250px"></div>
    <div class="head-logos">
      <div class="brand"><span class="brand-dot"></span>Luftprüfer.de</div>
      <div class="brand partner"><span class="brand-dot" style="width:16px;height:16px"></span>TESTOVAL</div>
    </div>
    <h1 class="title">MESSANLEITUNG</h1>
    <p class="subtitle">Für Radonmessungen von<br>Innenraumluft mit passiven<br>Radon Detektoren</p>
    <div class="hero" role="img" aria-label="Illustration of a house with trees in front of a city skyline"></div>
    <div class="hero-line"></div>

    <div class="step" style="top:218px">
      <span class="step-tag" style="top:-6px;right:-18px">Schritt 1</span>
      <h3>REGISTRIERUNG<br>UND ANMELDUNG</h3>
      <p>Wenn Sie Neukunde sind, legen Sie bitte zunächst ein neues Benutzerkonto auf unserem Online-Portal <span class="url">https://kunden.testoval.se/de</span> an. Anschließend können Sie die Radondetektoren registrieren. Vermerken Sie den <b>Start der Messung</b> (Datum und Uhrzeit), <b>die Messorte</b> (Raum und Etage) sowie die <b>9-stellige Seriennummer</b> der Detektoren, die Sie auf der Verpackung oder auf der Unterseite der jeweiligen Detektoren finden. Firmenkunden haben die Möglichkeit eine Excel-Datei als Hilfsmittel herunterzuladen, die Sie ausfüllen und dann wieder hochladen können.</p>
    </div>

    <div class="step" style="top:384px">
      <span class="step-tag" style="top:-6px;right:-18px">Schritt 2</span>
      <h3>PLATZIERUNG DER DETEKTOREN</h3>
      <p>Bevor Sie die Detektoren der Verpackung entnehmen, überlegen Sie wo genau Sie die Radondetektoren platzieren wollen.</p>
      <p><b>Die Radonmessung beginnt, sobald Sie die radondichten Verpackungen öffnen.</b></p>
      <p>Beachten Sie bei der Platzierung zunächst die Auswahl der Räume und die Positionierung der Radondetektoren im Raum.</p>
      <p>Für eine zuverlässige Radonmessung empfehlen wir wie folgt vorzugehen:</p>
      <p class="sub">➲ Die Auswahl der Räume</p>
      <p class="kind">Radonmessungen für Einfamilienhäuser:</p>
      <p>Es sollten mindestens zwei Wohnräume und pro bewohnte Etage mindestens ein Wohnraum gemessen werden.</p>
      <p>Wählen Sie Räume aus, in denen Sie sich oft aufhalten (z.B. das Wohn- und Schlafzimmer). Vermeiden Sie aber Räume, in denen das Fenster mehrere Stunden am Tag oder in der Nacht geöffnet ist.</p>
      <p>Insofern Sie einen Keller haben, empfehlen wir <span class="em">alle Kellerräume zu messen</span>, da hier meist das größte Risiko einer erhöhten Radonkonzentration erwartet wird.</p>
    </div>
  </div>
</section>

<section class="spread spread-2">
  <div class="page page-inner-left">
    <div class="edge-dots" style="left:24px"></div>
    <div class="step" style="top:28px;left:40px;right:30px">
      <p class="kind" style="margin-top:0">Radonmessungen für Mehrfamilienhäuser,<br>&nbsp;&nbsp;&nbsp;Wohnungen und Wohnkomplexe:</p>
      <p>Alle Wohnungen mit direktem Bodenkontakt sowie mindestens eine Wohnung pro Etage sollten gemessen werden.</p>
      <p>Wählen Sie dabei Wohnungen, die an Aufzügen oder Luftschächten liegen.</p>
      <p>In größeren Wohnkomplexen sollten insgesamt mindestens 20% aller Wohnungen in einem Gebäude gemessen werden.</p>
      <p>Es sollten mindestens zwei Wohnräume pro ausgewählte Wohnung gemessen werden.</p>
      <p>Wählen Sie Räume aus, in denen Sie sich oft aufhalten (z.B. das Wohn- und Schlafzimmer). Vermeiden Sie aber Räume, in denen das Fenster mehrere Stunden am Tag oder in der Nacht geöffnet ist.</p>
      <p class="em">Selbst bei einer Einzimmerwohnung sollten Sie zwei Detektoren aufstellen.</p>
      <p class="kind" style="margin-top:10px">Radonmessungen für Arbeitsplätze<br>&nbsp;&nbsp;&nbsp;und öffentliche Gebäude:</p>
      <p>Wählen Sie Räume, die regelmäßig mehr als vier Stunden pro Tag genutzt werden.</p>
      <p>Messen Sie alle unterirdischen Räumlichkeiten, da hier meist das größte Risiko einer erhöhten Radonkonzentration erwartet wird.</p>
      <p>Messen Sie alle Räume im Erdgeschoß.</p>
      <p class="em">Für größere Räumlichkeiten empfehlen wir einen Detektor pro 200 m².</p>
      <p>In den oberen Etagen sollten Sie mit mindestens zwei Detektoren, sowie mindestens einem Detektor pro 200 m² messen.</p>
      <p>Falls Ihr Arbeitsplatz in einem Radon-Vorsorgegebiet liegt und somit der Messpflicht unterliegt, muss die Messdauer von 12 Monaten eingehalten werden.</p>
      <p class="sub" style="margin-top:14px">➲ Platzierung der Detektoren im Raum:</p>
      <p class="dash">Platzieren Sie die Detektoren in einem Mindestabstand von 20 cm zu Wänden, 50 cm zu Abluftsventilen, sowie 1,50 m zu Fenstern, Außentüren, Zuluftsventilen und Heizkörpern.</p>
      <p class="dash">Stellen Sie die Detektoren nicht auf dem Boden, an starken Wärmequellen oder Luftströmen auf. Vermeiden Sie auch Räume mit hoher Luftfeuchtigkeit, wie zum Beispiel das Badezimmer.</p>
      <p class="dash">Die Detektoren können entweder stehend (auf einem Tisch, im Regal oder einer Schrankwand) oder hängend mitten im Raum (z.B. von einer Lampe) platziert werden.</p>
      <p class="dash">Stellen Sie die Detektoren während der gesamten Messdauer nicht um.</p>
      <p class="dash">Versuchen Sie nicht das Gehäuse der Detektoren zu öffnen und platzieren Sie diese immer außer Reichweite von Kindern.</p>
    </div>
  </div>

  <div class="page page-inner-right">
    <div class="edge-dots" style="right:26px;top:60px"></div>
    <div class="deco" role="img" aria-label="Faint clock icon" style="right:70px;top:64px;width:80px;height:80px;border-radius:50%"></div>
    <div class="step" style="top:32px">
      <span class="step-tag" style="top:-4px;right:-18px">Schritt 3</span>
      <h3 style="margin-bottom:6px">RADONMESSUNG</h3>
      <p class="hl" style="font-size:10.5px">Die Radonmessung beginnt, sobald Sie die<br>radondichten Verpackungen öffnen.</p>
      <p style="margin-top:10px"><b>Bitte halten Sie die Messdauer wie folgt ein:</b></p>
      <p class="kind" style="margin-top:10px">Kurzzeitmessung:</p>
      <p class="dash">Mindestmessdauer 10 Tage (bis hin zu 30 Tagen).</p>
      <p class="dash">Führen Sie die Messung vorzugsweise in der Heizperiode (1. Oktober – 30. April) durch.</p>
      <p class="dash">Kurzzeitmessungen werden oft beim Kauf oder Verkauf von Immobilien genutzt, um ein mögliches Gefährdungspotential abschätzen zu können, oder wenn die Zeit nicht ausreicht, um eine Langzeitmessung durchzuführen.</p>
      <p class="kind" style="margin-top:10px">Langzeitmessung:</p>
      <p class="dash">Mindestmessdauer 3 Monate während der Heizperiode (1. Oktober – 30. April).</p>
      <p class="dash">Um einen Jahresmittelwert der Radonkonzentration in Innenräumen ermitteln zu können, halten Sie die Messdauer von 12 Monaten ein.</p>
      <p class="dash"><b>Falls Ihr Arbeitsplatz in einem Radon-Vorsorgegebiet liegt und somit der Messpflicht unterliegt, muss die Messdauer von 12 Monaten eingehalten werden.</b></p>
    </div>

    <div class="deco" role="img" aria-label="Faint envelope icon" style="right:70px;top:450px;width:90px;height:80px"></div>
    <div class="step" style="top:374px">
      <span class="step-tag" style="top:-4px;right:-18px">Schritt 4</span>
      <h3>ABSCHLUSS DER RADONMESSUNG<br>MIT ABSCHLIESSENDEM PRÜFBERICHT</h3>
      <p>Nach Ablauf der Messdauer, loggen Sie sich auf<br><span class="url">https://kunden.testoval.se/de</span> in Ihrem Account ein.</p>
      <p style="margin-top:8px">Vermerken Sie hier das Ende der Messung und senden Sie anschließend alle Radondetektoren ausreichend frankiert in einem Umschlag oder einem Karton zeitnah an unsere Rücksendeadresse:</p>
      <p class="addr">Luftprüfer.de<br>Lindenstraße 14</p>
      <p class="addr">27612 Musterdorf-Heide – Deutschland</p>
      <p style="margin-top:8px">Sobald die Radondetektoren im Labor von Testoval eingetroffen sind, werden diese fachgerecht analysiert und die Ergebnisse der Radonmessung ausgewertet. Ein vollständiger Prüfbericht wird Ihnen innerhalb 36 Stunden nach Erhalt der Detektoren im Labor per E-Mail zugeschickt.</p>
    </div>
    <div class="foot-logos" style="justify-content:flex-end;bottom:16px">
      <div class="brand"><span class="brand-dot"></span>Luftprüfer.de</div>
    </div>
  </div>
</section>

<p class="caption">Das Format des Flyer ist geschlossen DIN A5 (148,5 x 210 mm)<br>mit 4 Seiten, Offenes Format: DIN A4 (210 x 297 mm)</p>

<footer class="board-foot">
  <div class="brand"><span class="brand-dot"></span>TESTOVAL</div>
</footer>

</body>
</html>
```